Sunset Harbor Living Web Page

We need a web page design that has two intro pages - first being a 'home page', then a link to the second page that has the 'content tabs' and a 'call to action' (see below).

The business helps people that wish to retire to S.E.Asia (Thailand, Malaysia, Indonesia,The Philippines etc) - to enjoy the lifestyle and the remaining years of their lives. What attracts S.E.Asia to many people is the lower cost, the atmoshpere and beauty of the tropics and the vibrancy of the various countries.

People that are wishing to make the most of their retirement and are adventurous at a great bargain compared to the cost of their own countries will be interested.

We help them achieve this - visa, financials (tax, gov't payments etc), introduce them to the right people for property, clubs, retirement facilities, insurance and so forth.

Therefore we are providing an extremely wide ranging service and this site will provide broad but general information only - with a call to action to come and see us for more specific information and how we can help them specifically.

This site will be predominantly for travel and lifestyle, it will be linked with another financial services (financial planning) site later down the track.

The colour scheme is dark green and blue - as per the attached logo design. Photos and background just think lifestyle and S.E.Asia - beaches/mountains/water/recreational activities for retirees.

Target market is mostly those coming up to retirement to those that are already retired. But we also expect to have some interest with younger people that would like to find out more and plan for the future. So a broad age group but I would say mostly 40-70 yrs old.

On the first (Home) page we would like our company name 'Sunset Harbor Living', our logo (which will be on all pages) and a statement such as: “Imagine a retirement where your dreams are brought to life, and you have never felt more alive. Let us show you how”. Then a link to the second page.

We would like an uncluttered site. On the second (contents) page the tabs would be:

- Visa
- Property
- Financials
- Travel
- Insurance & Healthcare
- Medical Tourism
- Cost of living
- Weekly Blogs and articles
- Sunset Harbor Living story

We would also like a call to action on the second page - asking them to leave their contact details if they wish to learn more or sign up to our weekly newsletter/blog.

We are open to suggestions and your imaginations.

Thank you
Malcolm

Font styles to use
Serif
Script

Colors
0255a3
3377b5
00a990
9bcb3c
abd036
33b8a4
85abd2
cadf82
86cfc6

Requirements
Must have
• I have been asked by the web designer to receive a 'Web Font' so that we can 'get off of Zentrofy'. Hope that makes sense.

```html
<!DOCTYPE html>
<html lang="en">
<head>
<meta charset="utf-8">
<title>Sunset Harbor Living — Home</title>
<link rel="stylesheet" href="https://fonts.googleapis.com/css2?family=Abel&family=Mulish:wght@700;800&display=swap">
<style>
  :root {
    --sky-deep: #0b2350;
    --sky-mid: #1a3a6b;
    --water: #3f6a6a;
    --water-deep: #2d4f52;
    --brand-green: #1fb35a;
    --brand-blue: #0aa0dc;
    --white: #ffffff;
    --text-soft: #e9eef2;
  }
  * { margin: 0; padding: 0; box-sizing: border-box; }
  html, body { width: 1200px; height: 683px; overflow: hidden; background: var(--sky-deep); }
  .hero { position: relative; width: 1200px; height: 683px; overflow: hidden; }
  .hero-backdrop {
    position: absolute;
    inset: 0;
    background:
      radial-gradient(ellipse 420px 220px at 160px 250px, rgba(70,78,80,0.75), transparent 70%),
      radial-gradient(ellipse 300px 160px at 1030px 150px, rgba(120,140,170,0.35), transparent 70%),
      linear-gradient(180deg, var(--sky-deep) 0%, var(--sky-mid) 38%, #2c4a5a 52%, var(--water) 66%, var(--water-deep) 100%);
  }
  .brand {
    position: absolute;
    left: 0;
    right: 0;
    top: 264px;
    display: flex;
    justify-content: center;
    align-items: center;
    gap: 12px;
  }
  .brand-dot {
    width: 26px;
    height: 26px;
    border-radius: 50%;
    background: var(--brand-green);
  }
  .brand-name {
    font-family: "Mulish", sans-serif;
    font-weight: 800;
    font-size: 36px;
    line-height: 42px;
    color: var(--white);
    letter-spacing: -0.3px;
  }
  .brand-tagline {
    position: absolute;
    left: 0;
    right: 0;
    top: 302px;
    text-align: center;
    font-family: "Mulish", sans-serif;
    font-weight: 800;
    font-size: 11px;
    line-height: 14px;
    letter-spacing: 0.6px;
    color: var(--white);
  }
  .headline {
    position: absolute;
    left: 0;
    right: 0;
    top: 340px;
    font-family: "Abel", sans-serif;
    font-weight: 400;
    font-size: 33px;
    line-height: 49px;
    text-align: center;
    color: var(--text-soft);
  }
  .cta-button {
    position: absolute;
    left: 443px;
    top: 473px;
    display: flex;
    align-items: center;
    width: 333px;
    height: 55px;
    border: 2px solid var(--white);
    border-radius: 5px;
    background: var(--brand-green);
    overflow: hidden;
    text-decoration: none;
  }
  .cta-label {
    padding-left: 19px;
    font-family: "Mulish", sans-serif;
    font-weight: 700;
    font-size: 22px;
    color: var(--white);
  }
  .cta-arrow {
    position: absolute;
    right: 0;
    top: 0;
    width: 56px;
    height: 51px;
  }
</style>
</head>
<body>
  <main class="hero">
    <div class="hero-backdrop" role="img" aria-label="Tropical beach with granite boulders, palm trees and calm shallow turquoise water under a deep blue evening sky"></div>
    <div class="brand">
      <span class="brand-dot" aria-hidden="true"></span>
      <h1 class="brand-name">Sunset Harbor Living</h1>
    </div>
    <p class="brand-tagline">TROPICAL RETIREMENT GUIDES</p>
    <p class="headline">Imagine A Retirement Where Your Dreams Are Brought To Life,<br>&amp; You Have Never Felt More Alive</p>
    <a class="cta-button" href="#contents">
      <span class="cta-label">Let Us Show You How</span>
      <svg class="cta-arrow" viewBox="0 0 56 51" aria-hidden="true">
        <path d="M12 -1 H57 V52 H12 A30 30 0 0 1 12 -1 Z" fill="#0aa0dc" stroke="#ffffff" stroke-width="2"/>
        <path d="M17 17 L25 25.5 L17 34 M25 17 L33 25.5 L25 34" fill="none" stroke="#ffffff" stroke-width="2"/>
      </svg>
    </a>
  </main>
</body>
</html>
```